Verodex business card

Business card for sustainable investment company called "Verodex". Verodex is an exchange platform selling carbon credits between buyers and sellers. Carbon Credits are an environmental commodity for reducing global carbon emissions.

the card should obviously have our logo and the theme should be sustainability/environment mixed with a trading platform.

Contact Information for Business Card

Logo, Name, Title, Phone, Email

Colors
0054AA
0677BA
7BADD7
CADEEF
E8F1F8
0094D4
00A9DD
6FCCEA
C7EBF8
E9F6FB
00AB8E
00BBA5
67D7C9
C6EFE9
E9F9F6
59FF00
82FF00
B8FF75
E3FFCB
F4FFEA

```html
<!DOCTYPE html>
<html lang="en">
<head>
<meta charset="utf-8">
<title>Verodex business card</title>
<link href="https://fonts.googleapis.com/css2?family=Open+Sans:wght@300;400;700;800&display=swap" rel="stylesheet">
<style>
  :root {
    --page-bg: #e9edf2;
    --card-navy: #152a52;
    --accent-cyan: #4cc3e6;
    --text-white: #ffffff;
    --card-shadow: rgba(10, 20, 40, 0.22);
  }
  * { box-sizing: border-box; margin: 0; padding: 0; }
  html, body {
    width: 1200px;
    height: 856px;
    overflow: hidden;
    background: var(--page-bg);
    font-family: "Open Sans", Arial, sans-serif;
  }
  .sheet {
    width: 1200px;
    height: 856px;
    display: flex;
    flex-direction: column;
    align-items: center;
    justify-content: center;
    gap: 28px;
  }
  .card {
    width: 700px;
    height: 400px;
    background: var(--card-navy);
    box-shadow: 0 10px 28px var(--card-shadow);
    display: flex;
    align-items: center;
    justify-content: center;
  }
  /* Front: name and contacts */
  .card-front { gap: 26px; }
  .identity { text-align: right; }
  .identity-name {
    color: var(--accent-cyan);
    font-weight: 700;
    font-size: 30px;
    letter-spacing: -0.5px;
    line-height: 1.1;
  }
  .identity-title {
    color: var(--text-white);
    font-weight: 300;
    font-size: 20px;
    margin-top: 4px;
  }
  .divider {
    width: 2px;
    height: 96px;
    background: var(--accent-cyan);
  }
  .contacts { list-style: none; }
  .contact-item {
    display: flex;
    align-items: center;
    gap: 10px;
    color: var(--text-white);
    font-weight: 300;
    font-size: 20px;
    line-height: 1.45;
  }
  .contact-icon { width: 16px; height: 16px; flex: none; }
  /* Back: wordmark */
  .card-back { gap: 22px; }
  .brand-dot {
    width: 34px;
    height: 34px;
    border-radius: 50%;
    background: var(--accent-cyan);
  }
  .brand-name {
    color: var(--text-white);
    font-weight: 800;
    font-size: 84px;
    letter-spacing: 1px;
    line-height: 1;
  }
</style>
</head>
<body>
<main class="sheet">
  <section class="card card-front" aria-label="Business card front">
    <div class="identity">
      <p class="identity-name">DANIEL MORRIS</p>
      <p class="identity-title">Managing Director</p>
    </div>
    <div class="divider"></div>
    <ul class="contacts">
      <li class="contact-item">
        <svg class="contact-icon" viewBox="0 0 16 16" aria-hidden="true"><path d="M3.5 1.5l2.5 3-1.5 1.8c.9 2 2.4 3.5 4.3 4.4l1.7-1.5 3 2.4-1.2 2.4c-5.5-.3-10-4.8-10.3-10.3z" fill="var(--accent-cyan)"/></svg>
        <span>555 210 478</span>
      </li>
      <li class="contact-item">
        <svg class="contact-icon" viewBox="0 0 16 16" aria-hidden="true"><rect x="1" y="3" width="14" height="10" rx="1" fill="var(--accent-cyan)"/><path d="M1.5 3.8L8 9l6.5-5.2" stroke="var(--card-navy)" stroke-width="1.4" fill="none"/></svg>
        <span>info@verodexmail.com</span>
      </li>
      <li class="contact-item">
        <svg class="contact-icon" viewBox="0 0 16 16" aria-hidden="true"><circle cx="8" cy="8" r="7" fill="var(--accent-cyan)"/><path d="M1 8h14M8 1c-2.5 2.2-2.5 11.8 0 14M8 1c2.5 2.2 2.5 11.8 0 14" stroke="var(--card-navy)" stroke-width="1.1" fill="none"/></svg>
        <span>www.verodexsite.com</span>
      </li>
    </ul>
  </section>

  <section class="card card-back" aria-label="Business card back">
    <span class="brand-dot" aria-hidden="true"></span>
    <p class="brand-name">VERODEX</p>
  </section>
</main>
</body>
</html>
```